New Business Card Design Project

I need a design for business cards, i am an electrical business called "Corvane Electrical and Communications" i need the cards to be double sided with the company logo on the back (attached) the front needs to say my company name, web site, email address, telephone number, and ABN number and electrical license number. I am open to different arrangements of the information but would like the background to be incorporating something electrical or something that looks smart. open to all additional ideas also.

The company colours are orange and grey see logo attached.

Business Name: Corvane Electrical and Communications
Website: corvaneelectricalandcomms.example.com.au
Email: brent@corvaneelectricalandcomms.example.com.au
Telephone(mobile): 0481209736
ABN: 71208349162
Lic No: 418273D

Target Market(s)

Business entities, Project Managers, Accounts, Clients

Industry/Entity Type

Electrician

Contact Information for Business Card

I need a design for business cards, i am an electrical business called "Corvane Electrical and Communications" i need the cards to be double sided with the company logo on the back (attached) the front needs to say my company name

Font styles to use
Serif
Sans Serif

Colors
f37122
5c5c5c

Requirements
Must have
• Must have the Logo on the back open to different ways of it being on the back but had in mind to keep it central but again open to other options
Nice to have
• A real modern cool background that is eye catching yet contemporary
Should not have
• No backgrounds of a light bulb or plug or anything like that

```html
<!DOCTYPE html>
<html lang="en">
<head>
<meta charset="utf-8">
<title>Corvane Electrical and Communications – Business Cards</title>
<link rel="stylesheet" href="https://fonts.googleapis.com/css2?family=Open+Sans:wght@400;600&display=swap">
<style>
  :root {
    --backdrop: #2b2b2b;
    --card-black: #050505;
    --card-white: #ffffff;
    --brand-orange: #f3a21b;
    --brand-grey: #5c5c5c;
    --text-white: #ffffff;
  }
  html, body {
    margin: 0;
    width: 1200px;
    height: 900px;
    overflow: hidden;
    background: var(--backdrop);
    font-family: "Open Sans", Arial, sans-serif;
  }
  .sheet {
    width: 1200px;
    height: 900px;
    display: flex;
    flex-direction: column;
    align-items: center;
    justify-content: center;
    gap: 40px;
  }
  .card {
    position: relative;
    width: 700px;
    height: 400px;
    border-radius: 26px;
    overflow: hidden;
    background: var(--card-black);
    box-shadow: 0 10px 30px rgba(0,0,0,0.45);
  }

  /* Brand name block */
  .brand {
    position: absolute;
    display: flex;
    align-items: center;
    gap: 14px;
  }
  .brand-dot {
    width: 18px;
    height: 18px;
    border-radius: 50%;
    background: var(--brand-orange);
    flex: none;
  }
  .brand-name {
    margin: 0;
    font-weight: 600;
    color: var(--brand-orange);
    line-height: 1.15;
    letter-spacing: 0.5px;
  }

  /* Back of card */
  .card-back .brand { left: 150px; top: 140px; }
  .card-back .brand-name { font-size: 40px; }
  .card-back .website {
    position: absolute;
    right: 40px;
    bottom: 38px;
    margin: 0;
    font-size: 19px;
    color: var(--text-white);
  }

  /* Front of card */
  .card-front .wave {
    position: absolute;
    inset: 0;
    width: 700px;
    height: 400px;
  }
  .card-front .edge-tab {
    position: absolute;
    left: 0;
    top: 150px;
    width: 8px;
    height: 40px;
    background: var(--card-white);
  }
  .card-front .person {
    position: absolute;
    left: 34px;
    top: 128px;
  }
  .person-name {
    margin: 0;
    font-size: 30px;
    font-weight: 400;
    color: var(--brand-orange);
    letter-spacing: 0.5px;
  }
  .person-role {
    margin: 2px 0 0;
    font-size: 15px;
    color: var(--text-white);
  }
  .card-front .brand { right: 40px; top: 44px; }
  .card-front .brand-name { font-size: 27px; text-align: right; }
  .licence {
    position: absolute;
    right: 70px;
    top: 150px;
    margin: 0;
    font-size: 15px;
    color: var(--brand-orange);
  }
  .contact-list {
    position: absolute;
    left: 40px;
    bottom: 24px;
    margin: 0;
    padding: 0;
    list-style: none;
    font-size: 15px;
    color: var(--brand-grey);
  }
  .contact-list li {
    display: flex;
    align-items: center;
    gap: 10px;
    line-height: 24px;
  }
  .contact-label { color: var(--brand-orange); font-weight: 600; }
  .contact-icon { width: 14px; height: 14px; flex: none; }
</style>
</head>
<body>
<main class="sheet">

  <section class="card card-back" aria-label="Business card back">
    <div class="brand">
      <span class="brand-dot"></span>
      <p class="brand-name">Corvane Electrical<br>and Communications</p>
    </div>
    <p class="website">www.corvaneelectricalandcomms.example.com.au</p>
  </section>

  <section class="card card-front" aria-label="Business card front">
    <svg class="wave" viewBox="0 0 700 400" aria-hidden="true">
      <path d="M0 400 L0 345 C 150 240, 380 250, 520 220 C 610 200, 670 170, 700 140 L700 400 Z" fill="var(--card-white)"/>
      <path d="M0 345 C 150 240, 380 250, 520 220 C 610 200, 670 170, 700 140" fill="none" stroke="var(--brand-orange)" stroke-width="3"/>
    </svg>
    <span class="edge-tab"></span>
    <div class="person">
      <h1 class="person-name">MARLO TENNANT</h1>
      <p class="person-role">DIRECTOR</p>
    </div>
    <div class="brand">
      <span class="brand-dot"></span>
      <p class="brand-name">Corvane Electrical<br>and Communications</p>
    </div>
    <p class="licence">Lic No: 418273D</p>
    <ul class="contact-list">
      <li><span class="contact-label">ABN:</span> 71208349162</li>
      <li>
        <svg class="contact-icon" viewBox="0 0 16 16" aria-hidden="true"><path d="M3 1h3l1.5 4-2 1.3a9 9 0 0 0 4.2 4.2L11 8.5l4 1.5v3a2 2 0 0 1-2 2A12 12 0 0 1 1 3a2 2 0 0 1 2-2z" fill="var(--brand-orange)"/></svg>
        0481-209-736
      </li>
      <li>
        <svg class="contact-icon" viewBox="0 0 16 16" aria-hidden="true"><rect x="1" y="3" width="14" height="10" rx="1" fill="none" stroke="var(--brand-orange)" stroke-width="1.6"/><path d="M1.5 4 8 9l6.5-5" fill="none" stroke="var(--brand-orange)" stroke-width="1.6"/></svg>
        brent@corvaneelectricalandcomms.example.com.au
      </li>
      <li>
        <svg class="contact-icon" viewBox="0 0 16 16" aria-hidden="true"><circle cx="8" cy="8" r="6.5" fill="none" stroke="var(--brand-orange)" stroke-width="1.5"/><path d="M1.5 8h13M8 1.5c-3 3.5-3 9.5 0 13M8 1.5c3 3.5 3 9.5 0 13" fill="none" stroke="var(--brand-orange)" stroke-width="1.2"/></svg>
        www.corvaneelectricalandcomms.example.com.au
      </li>
    </ul>
  </section>

</main>
</body>
</html>
```